The quiet harbor with an elephant incorporated in the background

Target Market(s)

Real estate

Industry/Entity Type

Real Estate

Contact Information for Business Card

On back on want my name & number
In front I want the business name, "the quiet harbor", below to say staging & design

Logo Text

The quiet harbor

Font styles to use
Serif

Colors
000000

Requirements
Must have
• I want an elephant behind the writing in gold transperant

```html
<!DOCTYPE html>
<html lang="en">
<head>
<meta charset="utf-8">
<title>The Quiet Harbor — Business Card</title>
<link rel="stylesheet" href="https://fonts.googleapis.com/css2?family=Cormorant+Garamond:wght@500;600&display=swap">
<style>
  :root {
    --page-bg: #c4c4c4;
    --card-bg: #111111;
    --card-ink: #ffffff;
    --tagline-ink: #d9d2c4;
    --elephant-tone: #3a3127;
    --elephant-edge: #1a1713;
  }
  * { margin: 0; padding: 0; box-sizing: border-box; }
  html, body {
    width: 1200px;
    height: 1000px;
    overflow: hidden;
    background: var(--page-bg);
    font-family: "Cormorant Garamond", "Garamond", serif;
  }
  .sheet {
    position: relative;
    width: 1200px;
    height: 1000px;
    display: flex;
    align-items: center;
    justify-content: center;
    gap: 60px;
  }
  .card {
    position: relative;
    width: 520px;
    height: 300px;
    background: var(--card-bg);
    color: var(--card-ink);
    box-shadow: 0 4px 14px rgba(0, 0, 0, 0.35);
    overflow: hidden;
  }
  .name-frame,
  .brand-frame {
    position: absolute;
    left: 50%;
    transform: translateX(-50%);
    border: 2px solid var(--card-ink);
    text-align: center;
    text-transform: uppercase;
    font-weight: 600;
    white-space: nowrap;
    line-height: 1.2;
  }
  .name-frame {
    top: 122px;
    width: 292px;
    padding: 4px 0 3px;
    font-size: 21px;
    letter-spacing: 0.2em;
  }
  .contact-line {
    position: absolute;
    left: 0;
    right: 0;
    bottom: 16px;
    text-align: center;
    font-size: 12px;
    font-weight: 600;
    letter-spacing: 0.06em;
  }
  .elephant-art {
    position: absolute;
    left: 95px;
    top: 0;
    width: 370px;
    height: 300px;
  }
  .brand-frame {
    top: 132px;
    width: 322px;
    padding: 4px 0 3px;
    font-size: 19px;
    letter-spacing: 0.08em;
    background: rgba(17, 17, 17, 0.25);
  }
  .brand-tagline {
    position: absolute;
    left: 0;
    right: 0;
    top: 176px;
    text-align: center;
    font-size: 13px;
    font-weight: 500;
    letter-spacing: 0.3em;
    text-transform: uppercase;
    color: var(--tagline-ink);
  }
</style>
</head>
<body>
  <main class="sheet">
    <section class="card card--back" aria-label="Card back">
      <h1 class="name-frame">Adrian Bell</h1>
      <p class="contact-line">000 000 0000 | info@yourmail.com | www.yourweb.com</p>
    </section>

    <section class="card card--front" aria-label="Card front">
      <svg class="elephant-art" viewBox="0 0 370 300" role="img" aria-label="Faint gold elephant figure in the background">
        <defs>
          <radialGradient id="elephantGlow" cx="50%" cy="42%" r="55%">
            <stop offset="0%" stop-color="var(--elephant-tone)" stop-opacity="0.8"/>
            <stop offset="100%" stop-color="var(--elephant-edge)" stop-opacity="0"/>
          </radialGradient>
        </defs>
        <rect x="0" y="0" width="370" height="300" fill="url(#elephantGlow)"/>
      </svg>
      <h2 class="brand-frame">The Quiet Harbor</h2>
      <p class="brand-tagline">Staging &amp; Design</p>
    </section>
  </main>
</body>
</html>
```